Calvanto Group Real Estate Company business cards

New business card design, we are generally happy with the basic layout of the existing front of business card, (feel free to change) but require a head shot photo on the back side.

http://www.calvanto.com.au/

Attached logos, and existing business card

------------------------------

Target Market(s)

Real estate

Industry/Entity Type

Real Estate

Contact Information for Business Card

Standard size double sided

Font styles to use
Other font styles liked:
• Futura

Requirements
Must have
• Photo head shot on the back side
Nice to have
• yes
Should not have
• No

```html
<!DOCTYPE html>
<html lang="en">
<head>
<meta charset="utf-8">
<title>Calvanto Group – Business Cards</title>
<link href="https://fonts.googleapis.com/css2?family=Jost:ital,wght@0,400;0,500;0,600;1,600&display=swap" rel="stylesheet">
<style>
  :root {
    --page: #e6e6e8;
    --purple: #3b1f6b;
    --purple-deep: #24103f;
    --purple-mid: #4a2a80;
    --orange: #f0891c;
    --white: #ffffff;
    --card-white: #f7f7f9;
    --ink: #2b2440;
    --photo-tone: #e9eaee;
  }
  * { box-sizing: border-box; margin: 0; padding: 0; }
  html, body { width: 1200px; height: 1200px; overflow: hidden; }
  body {
    background: var(--page);
    font-family: "Jost", "Futura", sans-serif;
    position: relative;
  }
  .card {
    position: absolute;
    left: 180px;
    width: 840px;
    height: 480px;
    border-radius: 28px;
    overflow: hidden;
    box-shadow: 0 6px 18px rgba(0,0,0,0.18);
  }

  /* Front */
  .card--front {
    top: 80px;
    background: linear-gradient(135deg, var(--purple-mid) 0%, var(--purple) 45%, var(--purple-deep) 100%);
  }
  .tagline {
    position: absolute;
    left: 56px;
    top: 150px;
    color: var(--white);
    font-size: 44px;
    font-weight: 400;
    line-height: 1.1;
  }
  .tagline .accent { color: var(--orange); }
  .front-brand {
    position: absolute;
    left: 56px;
    bottom: 64px;
    color: var(--white);
    font-size: 62px;
    font-weight: 500;
    line-height: 1;
    letter-spacing: 1px;
  }
  .headshot {
    position: absolute;
    top: 22px;
    right: 22px;
    width: 400px;
    height: 330px;
    background: linear-gradient(180deg, #f2f3f6 0%, var(--photo-tone) 60%, #c9ccd8 100%);
  }

  /* Back */
  .card--back {
    top: 630px;
    background: var(--card-white);
  }
  .card--back svg.waves { position: absolute; inset: 0; }
  .person {
    position: absolute;
    top: 28px;
    right: 56px;
    text-align: right;
    color: var(--white);
  }
  .person-name { font-size: 30px; font-weight: 600; font-style: italic; line-height: 1.2; }
  .person-role { font-size: 17px; font-weight: 400; margin-top: 2px; }
  .contacts {
    position: absolute;
    left: 56px;
    top: 282px;
    list-style: none;
    color: var(--ink);
    font-size: 19px;
  }
  .contacts li { display: flex; align-items: center; gap: 14px; height: 28px; }
  .contacts svg { width: 18px; height: 18px; flex: none; }
  .back-brand {
    position: absolute;
    left: 56px;
    bottom: 44px;
    color: var(--purple-deep);
    font-size: 64px;
    font-weight: 500;
    line-height: 1;
    letter-spacing: 1px;
  }
  .company-info {
    position: absolute;
    right: 56px;
    top: 282px;
    color: var(--ink);
    font-size: 18px;
    text-align: right;
    line-height: 30px;
  }
  .social { display: inline-flex; gap: 5px; vertical-align: middle; margin-left: 8px; }
  .social span { width: 20px; height: 20px; border-radius: 4px; background: var(--orange); display: inline-block; }
</style>
</head>
<body>

  <section class="card card--front" aria-label="Business card front">
    <p class="tagline">Let us<br>show you<br><span class="accent">property</span></p>
    <p class="front-brand">calvanto group</p>
    <div class="headshot" role="img" aria-label="Head shot photo of the director in a suit and tie"></div>
  </section>

  <section class="card card--back" aria-label="Business card back">
    <svg class="waves" viewBox="0 0 840 480" aria-hidden="true">
      <path d="M0 0 H840 V110 C620 115 420 140 240 175 C140 195 60 215 0 250 Z" fill="var(--purple)"/>
      <path d="M0 250 C60 215 140 195 240 175 C420 140 620 115 840 110 V122 C620 128 420 155 250 190 C150 210 60 235 0 266 Z" fill="var(--orange)"/>
      <path d="M12 270 C110 228 250 200 450 172" fill="none" stroke="var(--orange)" stroke-width="4" stroke-linecap="round"/>
    </svg>

    <div class="person">
      <p class="person-name">Daniel Tran</p>
      <p class="person-role">Director</p>
    </div>

    <ul class="contacts">
      <li>
        <svg viewBox="0 0 20 20" aria-hidden="true"><rect x="5" y="1" width="10" height="18" rx="2" fill="var(--orange)"/><rect x="7" y="4" width="6" height="10" fill="var(--white)"/></svg>
        0400 555 018
      </li>
      <li>
        <svg viewBox="0 0 20 20" aria-hidden="true"><circle cx="10" cy="10" r="8" fill="var(--orange)"/><path d="M2 10 H18 M10 2 C6 6 6 14 10 18 M10 2 C14 6 14 14 10 18" stroke="var(--white)" stroke-width="1.3" fill="none"/></svg>
        www.calvanto.com.au
      </li>
      <li>
        <svg viewBox="0 0 20 20" aria-hidden="true"><rect x="1" y="4" width="18" height="12" rx="1" fill="var(--orange)"/><path d="M1 4 L10 11 L19 4" stroke="var(--white)" stroke-width="1.5" fill="none"/></svg>
        daniel.tran@calvanto.com.au
      </li>
    </ul>

    <div class="company-info">
      <p>Find us:<span class="social" aria-hidden="true"><span></span><span></span><span></span></span></p>
      <p>ABN: 12 345 678 901</p>
    </div>

    <p class="back-brand">calvanto group</p>
  </section>

</body>
</html>
```